Maple Hollow Ranch Business Card

Farm selling Nigerian Dwarf Goats, Bison, chickens, and miniature donkeys. Additionally we sell goats milk, goats milk soap and goat cheese, bison meat, bison heads, and bison skins, and chicken eggs.
Address 4127 Tanager Lane
Hopkinsville, KY 42316
Phone number 615-392-5174
Website: MapleHollowRanch@quailmail.example
I will upload my farm logo, cheese label, and soap label to give you ideas of my theme.
I want a really catchy card that people will remember.

```html
<!DOCTYPE html>
<html lang="en">
<head>
<meta charset="utf-8">
<title>Maple Hollow Ranch Business Card</title>
<link rel="stylesheet" href="https://fonts.googleapis.com/css2?family=Exo+2:wght@400;500;600&display=swap">
<style>
  :root {
    --stage: #1c1a19;
    --card-dark: #2d2520;
    --gold: #e8a912;
    --gold-text: #e2a71c;
    --rust: #8b5a1e;
    --ink: #3a2a14;
    --badge-fill: #5e3f18;
  }
  * { margin: 0; padding: 0; box-sizing: border-box; }
  html, body { width: 1200px; height: 881px; overflow: hidden; }
  body {
    background: var(--stage);
    font-family: "Exo 2", sans-serif;
    position: relative;
  }
  .card {
    position: absolute;
    width: 540px;
    height: 309px;
    background: var(--card-dark);
    overflow: hidden;
    box-shadow: 0 10px 30px rgba(0,0,0,.45);
  }
  .card-back { left: 150px; top: 110px; }
  .card-front { left: 510px; top: 462px; }

  /* Brand lockup: plain circle + name */
  .brand-badge {
    position: absolute;
    border-radius: 50%;
    background: var(--badge-fill);
    border: 3px solid var(--rust);
  }
  .brand-name {
    position: absolute;
    color: var(--gold-text);
    font-weight: 600;
    letter-spacing: 1px;
    text-transform: uppercase;
    white-space: nowrap;
  }

  .card-back .brand-badge { left: 150px; top: 82px; width: 98px; height: 98px; }
  .card-back .brand-name { left: 258px; top: 120px; font-size: 17px; line-height: 22px; }
  .web-band {
    position: absolute;
    left: 322px; top: 220px;
    width: 218px; height: 26px;
    background: var(--gold);
    color: var(--ink);
    font-size: 10.5px;
    line-height: 26px;
    padding-left: 28px;
  }

  .front-shapes { position: absolute; inset: 0; }
  .contact-name {
    position: absolute; left: 38px; top: 28px;
    color: var(--ink); font-size: 15px; font-weight: 600; letter-spacing: 1px;
  }
  .contact-title {
    position: absolute; left: 38px; top: 48px;
    color: var(--ink); font-size: 11px;
  }
  .contact-address {
    position: absolute; left: 38px; top: 88px;
    color: var(--ink); font-size: 12px; line-height: 16px;
  }
  .contact-list {
    position: absolute; left: 38px; top: 168px;
    list-style: none; color: var(--ink); font-size: 10.5px;
  }
  .contact-list li { display: flex; align-items: center; gap: 7px; height: 19px; }
  .contact-list svg { width: 10px; height: 10px; fill: var(--ink); flex: none; }

  .card-front .brand-badge { left: 372px; top: 62px; width: 100px; height: 100px; }
  .card-front .brand-name {
    left: 302px; top: 184px; width: 240px;
    text-align: center; font-size: 15px; line-height: 20px;
  }
</style>
</head>
<body>

  <section class="card card-back" aria-label="Business card back">
    <div class="brand-badge" aria-hidden="true"></div>
    <div class="brand-name">Maple Hollow Ranch</div>
    <div class="web-band">www.maplehollowranch.example</div>
  </section>

  <section class="card card-front" aria-label="Business card front">
    <svg class="front-shapes" viewBox="0 0 540 309" width="540" height="309" aria-hidden="true">
      <path d="M0 0 H345 C300 80 270 200 265 309 H0 Z" fill="var(--gold)"/>
      <path d="M345 0 H363 C318 80 286 200 283 309 H265 C270 200 300 80 345 0 Z" fill="var(--rust)"/>
    </svg>

    <div class="contact-name">DANIEL WHITFIELD</div>
    <div class="contact-title">Managing Director</div>
    <div class="contact-address">4127 Tanager Lane<br>Hopkinsville, KY 42316</div>

    <ul class="contact-list">
      <li><svg viewBox="0 0 10 10"><path d="M2 0 L4 2.5 L3 3.6 Q4.5 6 6.4 7 L7.5 6 L10 8 L8.5 10 Q3 9 0 2 Z"/></svg>615-392-5174</li>
      <li><svg viewBox="0 0 10 10"><rect x="2.5" y="0" width="5" height="10" rx="1"/></svg>615-392-5174</li>
      <li><svg viewBox="0 0 10 10"><rect x="0" y="3" width="10" height="6" rx="1"/><rect x="2" y="0" width="6" height="3"/></svg>615-392-5174</li>
      <li><svg viewBox="0 0 10 10"><path d="M0 2 H10 V8 H0 Z M0 2 L5 6 L10 2"/></svg>MapleHollowRanch@quailmail.example</li>
      <li><svg viewBox="0 0 10 10"><circle cx="5" cy="5" r="4.5" fill="none" stroke="#3a2a14" stroke-width="1.2"/></svg>www.maplehollowranch.example</li>
    </ul>

    <div class="brand-badge" aria-hidden="true"></div>
    <div class="brand-name">Maple Hollow Ranch</div>
  </section>

</body>
</html>
```